Need a new updated business logo and business cards and possible car signs. Logo should be modern with bold elements. Possible use in some way of former logo may be considered. Looking for use of bold colors to grab attention with car signage/wrap in mind. Phone number should be easy to read- customers should understand what business is about- home painting, repair, renovation, 're-imagine your space' etc.

Target Market(s)

Homeowners, construction, businesses

Industry/Entity Type

Contractor

Contact Information for Business Card

Brennick Painting & Renovation, Inc.
Owner : Marcus D. Brennick
555-014-7382
marcusdbrennickmb@quillpost.net
All work is guaranteed and insured! More than 30 years of experience:
residential & commercial, Interior & Exterior, Renovation/Restoration

Logo Text

Brennick Painting & Renovation, Inc. 'Hard Working & Trustworthy'

Font styles to use
Other font styles liked:
• Designer suggestions for industry

Colors

Designer to choose colors to be used in the design.

Requirements
Must have
• New design logo-possibly incorporating old elements- new logo ok without old though as well. Cell Phone number has to be on there- Color preferable
Nice to have
• Nice to have a logo that pops and that may be used in conjunction with his parent company Brennick REAL Property, LLC.
• Business card layout of information that is clear & easy to read
Should not have
• Bulky old fonts

```html
<!DOCTYPE html>
<html lang="en">
<head>
<meta charset="utf-8">
<title>Brennick's Painting &amp; Renovation – Business Card</title>
<link href="https://fonts.googleapis.com/css2?family=Cinzel:wght@500;600&family=Lato:wght@400;700&display=swap" rel="stylesheet">
<style>
  :root {
    --backdrop: #2b2b2d;
    --card-white: #f3f3f3;
    --card-black: #1c1c1e;
    --pattern-tone: #2a2a2c;
    --navy: #163a66;
    --ink: #1f1f1f;
    --rule: #8c8c8c;
    --light-text: #f4f4f4;
  }
  * { box-sizing: border-box; margin: 0; padding: 0; }
  html, body { width: 1200px; height: 1108px; overflow: hidden; }
  body {
    background: var(--backdrop);
    font-family: "Lato", Arial, sans-serif;
    position: relative;
  }
  .card {
    position: absolute;
    top: 204px;
    width: 420px;
    height: 700px;
    border-radius: 26px;
    overflow: hidden;
    text-align: center;
  }
  .card-front { left: 150px; background: var(--card-white); color: var(--ink); }
  .card-back { left: 630px; background: var(--card-black); color: var(--light-text); }

  /* front */
  .brand {
    margin-top: 100px;
    display: flex;
    flex-direction: column;
    align-items: center;
  }
  .brand-mark {
    width: 64px;
    height: 64px;
    background: var(--navy);
    margin-bottom: 22px;
  }
  .brand-name {
    font-family: "Cinzel", Georgia, serif;
    font-weight: 600;
    color: var(--navy);
    font-size: 24px;
    line-height: 1.25;
    letter-spacing: 1px;
  }
  .person {
    margin-top: 52px;
  }
  .person-name {
    font-family: "Cinzel", Georgia, serif;
    font-weight: 600;
    color: var(--navy);
    font-size: 27px;
    letter-spacing: 1px;
  }
  .person-role { font-size: 21px; margin-top: 2px; }
  .rule {
    width: 200px;
    height: 1px;
    background: var(--rule);
    margin: 16px auto;
  }
  .contact { font-size: 21px; line-height: 1.35; }
  .company {
    font-weight: 700;
    color: var(--navy);
    font-size: 21px;
    line-height: 1.35;
  }
  .address { font-size: 21px; line-height: 1.35; }

  /* back */
  .back-pattern {
    position: absolute;
    inset: 0;
    background: linear-gradient(160deg, var(--pattern-tone), var(--card-black));
  }
  .back-copy {
    position: relative;
    padding-top: 300px;
  }
  .back-headline {
    font-family: "Cinzel", Georgia, serif;
    font-weight: 500;
    font-size: 25px;
    line-height: 1.3;
    letter-spacing: 1px;
  }
  .back-experience { font-size: 19px; margin-top: 24px; }
  .back-services { font-size: 19px; line-height: 1.35; margin-top: 26px; list-style: none; }
</style>
</head>
<body>
  <section class="card card-front" aria-label="Business card front">
    <div class="brand">
      <div class="brand-mark"></div>
      <div class="brand-name">Brennick's<br>Painting &amp; Renovation, Inc</div>
    </div>
    <div class="person">
      <div class="person-name">Marcus D. Brennick</div>
      <div class="person-role">Owner</div>
    </div>
    <div class="rule"></div>
    <div class="contact">
      <div>555-014-7382</div>
      <div>marcusdbrennickmb@quillpost.net</div>
    </div>
    <div class="rule"></div>
    <div class="company">Brennick's Painting and Renovation</div>
    <div class="address">48 Alder Lane<br>Fairmont, NC 28340</div>
  </section>

  <section class="card card-back" aria-label="Business card back">
    <div class="back-pattern" role="img" aria-label="Faint repeating company mark pattern in dark grey"></div>
    <div class="back-copy">
      <div class="back-headline">All work is guaranteed<br>and insured!</div>
      <p class="back-experience">More than 30 years of experience.</p>
      <ul class="back-services">
        <li>Residential &amp; commercial</li>
        <li>Interior &amp; Exterior</li>
        <li>Renovation/Restoration</li>
      </ul>
    </div>
  </section>
</body>
</html>
```